Need a new company business card

I am looking for a new company business card. Front and back. With information on it as per below. Card should be professional. Yet clever. Simple. Modern design. Pim card, traditional size. OK with say, all black or all red backside.

Varnholt is an indie, bootstrapped magazine advancing the work of intersectional feminists busting their buts to create a just world through the power of enterprise and innovation.

Varnholt is the home and voice of entrepreneurial feminism and feminist innovators worldwide. Entrepreneurial feminists are people (of all genders) who see inequality as an innovation priority. They work to advance gender equity and/or who strive to integrate and practice feminist principles, pedagogy, values into their innovation and entrepreneurship work.
We are committed to this space being trans and queer inclusive, anti-racist, intersectional, brave, and safe. We welcome all allies. We value learning, edgy but civil discourse and integrative thinking skills.

Target Market(s)

feminists, business owners,

Industry/Entity Type

Publishing Company

Contact Information for Business Card

RD Tolliver
Founder/Publisher
4-237 Ashgrove Lane, Toronto, ON
M4T 2K8
publisher@varnholt.com
416-552-3019
www.varnholt.com

Font styles to use
Serif
Other font styles liked:
• Myriad Pro

Colors
ec1f27
000000
ffffff

Requirements
Must have
• logo
• use red, black white colours only.
Nice to have
• use the compass in pattern or creatively but not too busy please
Should not have
• Should not be too busy. Elegant.

```html
<!DOCTYPE html>
<html lang="en">
<head>
<meta charset="utf-8">
<title>Varnholt – Business Card</title>
<link href="https://fonts.googleapis.com/css2?family=Roboto:wght@400;500;700&display=swap" rel="stylesheet">
<style>
  :root {
    --brand-red: #d42a26;
    --ink: #2b2b2b;
    --card-face: #f3f2f0;
    --backdrop: #dcd8d3;
  }
  html, body {
    margin: 0;
    padding: 0;
    width: 1200px;
    height: 1054px;
    overflow: hidden;
    background: var(--backdrop);
    font-family: "Roboto", Arial, sans-serif;
  }
  .business-card {
    position: absolute;
    left: 120px;
    top: 238px;
    width: 960px;
    height: 578px;
    background: var(--card-face);
    box-sizing: border-box;
    border-bottom: 6px solid var(--brand-red);
    box-shadow: 0 6px 24px rgba(0, 0, 0, 0.12);
  }
  .brand-mark {
    position: absolute;
    left: 131px;
    top: 252px;
    display: flex;
    align-items: center;
    gap: 16px;
  }
  .brand-mark__dot {
    width: 34px;
    height: 34px;
    border-radius: 50%;
    background: var(--brand-red);
  }
  .brand-mark__name {
    font-size: 58px;
    font-weight: 700;
    color: var(--brand-red);
    line-height: 1;
  }
  .contact-block {
    position: absolute;
    left: 555px;
    top: 148px;
    color: var(--ink);
  }
  .contact-block__name {
    margin: 0;
    font-size: 38px;
    font-weight: 700;
    line-height: 1.1;
  }
  .contact-block__title {
    margin: 6px 0 0;
    font-size: 22px;
    color: var(--brand-red);
  }
  .contact-block__address {
    margin: 36px 0 0;
    font-size: 22px;
    line-height: 32px;
    font-style: normal;
  }
  .contact-list {
    list-style: none;
    margin: 22px 0 0;
    padding: 0;
    font-size: 22px;
  }
  .contact-list__item {
    display: flex;
    align-items: center;
    gap: 16px;
    height: 31px;
  }
  .contact-list__icon {
    width: 20px;
    height: 20px;
    fill: var(--brand-red);
    flex: none;
  }
</style>
</head>
<body>
  <section class="business-card">
    <div class="brand-mark">
      <span class="brand-mark__dot"></span>
      <span class="brand-mark__name">Varnholt</span>
    </div>

    <div class="contact-block">
      <h1 class="contact-block__name">RD Tolliver</h1>
      <p class="contact-block__title">Founder/Publisher</p>
      <address class="contact-block__address">4-237 Ashgrove Lane,<br>Toronto, ON M4T 2K8</address>
      <ul class="contact-list">
        <li class="contact-list__item">
          <svg class="contact-list__icon" viewBox="0 0 20 20" aria-hidden="true">
            <path d="M3 5c0-2 2-3 7-3s7 1 7 3v2h-4V5H7v2H3z"/>
            <path d="M5 9h10l2 8H3z"/>
          </svg>
          <span>416-552-3019</span>
        </li>
        <li class="contact-list__item">
          <svg class="contact-list__icon" viewBox="0 0 20 20" aria-hidden="true">
            <path d="M2 4h16v12H2z M3 5l7 6 7-6" fill="var(--brand-red)"/>
            <path d="M3 5l7 6 7-6" fill="none" stroke="#fff" stroke-width="1.5"/>
          </svg>
          <span>publisher@varnholt.com</span>
        </li>
        <li class="contact-list__item">
          <svg class="contact-list__icon" viewBox="0 0 20 20" aria-hidden="true">
            <circle cx="10" cy="10" r="8"/>
            <path d="M2 10h16M10 2v16M10 2c-4 4-4 12 0 16M10 2c4 4 4 12 0 16" fill="none" stroke="#fff" stroke-width="1.2"/>
          </svg>
          <span>www.varnholt.com</span>
        </li>
      </ul>
    </div>
  </section>
</body>
</html>
```